Vielen Dank für die Zusammenarbeit - die Korrekturen wurden sorgfältig, sehr schnell und gut umgesetzt.
Zielgruppe
Wir haben ein Bed and Breakfast am Sorpesee in Sundern. Die Zimmer sind individuell, mit Liebe eingerichtet. Wir bieten ein außergewöhnliches Frühstück. Unsere Zielgruppe sind sportliche Menschen (Motorradfahrer, Radfahrer, Wanderer etc.) die hier rund um unser Haus ein außergewöhnlich gutes Angebot finden. Uns hebt ein großer Garten und ein einzigartiges Kamin/Grillzimmer von den üblichen Häusern ab.
Aufgabenstellung
So individuell wie unser Haus soll auch der Flyer sein. Weniger Text - mehr Emotionen durch Bilder. Bitte schon einmal die Bilder von der Homepage ansehen - diese werden noch durch ein zwei drei Gartenfotos ergänzt. Farben und Schriften sollten sich ebenfalls hieran orientieren.

```html
<!DOCTYPE html>
<html lang="de">
<head>
<meta charset="utf-8">
<title>Flyer Innenseite – Bed and Breakfast am Sorpesee</title>
<link rel="stylesheet" href="https://fonts.googleapis.com/css2?family=Montserrat:wght@300;400;600;700&display=swap">
<style>
  :root {
    --wine: #7d1232;
    --wine-dark: #6a0d29;
    --white: #ffffff;
    --band-blue: #3c64a8;
    --band-yellow: #d6d58a;
  }
  * { margin: 0; padding: 0; box-sizing: border-box; }
  html, body { width: 1200px; height: 1200px; overflow: hidden; }
  body {
    font-family: "Montserrat", sans-serif;
    color: var(--white);
    background: linear-gradient(90deg, #8c1f43 0%, var(--wine) 35%, var(--wine-dark) 50%, var(--wine) 65%, #8a1d41 100%);
    position: relative;
  }
  .backdrop { position: absolute; inset: 0; width: 1200px; height: 1200px; }

  .rooms-intro { position: absolute; left: 0; top: 19px; width: 606px; text-align: center; }
  .rooms-intro h2 { font-weight: 600; font-size: 20.5px; line-height: 24px; letter-spacing: 0.3px; margin-bottom: 16px; }
  .rooms-intro p { font-weight: 400; font-size: 15.5px; line-height: 22px; letter-spacing: 0.3px; }

  .room { position: absolute; left: 0; width: 518px; }
  .room .photo { position: absolute; inset: 0; }
  .room .label {
    position: absolute; left: 0; top: 0; width: 100%; height: 56px;
    font-weight: 300; font-size: 37px; line-height: 56px; padding-left: 15px;
    text-shadow: 0 2px 3px rgba(0,0,0,.45);
  }
  .room .underline { position: absolute; left: 0; bottom: -9px; width: 100%; height: 9px; }
  .room--blue { top: 245px; height: 263px; }
  .room--blue .photo { background: linear-gradient(120deg, #d8d6cc 0%, #8a7d6c 30%, #1e3c78 55%, #2a2a30 100%); }
  .room--blue .label { background: rgba(60,100,168,.6); }
  .room--blue .underline { background: var(--band-blue); }
  .room--gold { top: 517px; height: 263px; }
  .room--gold .photo { background: linear-gradient(160deg, #f2f0ea 0%, #dcd7cc 45%, #4a4a4c 70%, #e6e47a 100%); }
  .room--gold .label { background: rgba(214,213,138,.75); }
  .room--gold .underline { background: var(--band-yellow); }
  .room--silver { top: 789px; height: 272px; }
  .room--silver .photo { background: linear-gradient(120deg, #6f8a5e 0%, #d9dcd6 35%, #f3f3f1 55%, #b38a55 80%, #3a3e48 100%); }
  .room--silver .label { background: rgba(200,200,200,.55); }

  .rooms-more { position: absolute; left: 0; top: 1107px; width: 600px; text-align: center; font-weight: 700; font-size: 20px; line-height: 28px; }

  .feature { position: absolute; left: 668px; width: 532px; }
  .feature .photo { position: absolute; left: 0; top: 0; width: 100%; height: 211px; }
  .feature h3 {
    position: absolute; left: 0; top: 0; width: 100%; height: 51px;
    font-weight: 600; font-size: 31px; line-height: 51px; padding-left: 25px;
    background: rgba(125,18,50,.72); letter-spacing: 0.5px;
  }
  .feature .copy { position: absolute; left: 0; top: 233px; width: 514px; font-size: 15px; line-height: 18.8px; letter-spacing: 0.3px; }
  .copy .line { display: block; text-align: justify; text-align-last: justify; white-space: nowrap; }
  .copy .line--last { text-align-last: left; }
  .feature--breakfast { top: 15px; }
  .feature--breakfast .photo { background: linear-gradient(110deg, #efe8dc 0%, #e9c97a 30%, #c78c4e 55%, #f0b53a 75%, #a8553a 100%); }
  .feature--leisure { top: 415px; }
  .feature--leisure .copy { top: 235px; }
  .feature--leisure .photo { background: linear-gradient(120deg, #4a3a30 0%, #c9bfb0 35%, #d6cfc4 55%, #b8202a 80%, #3a2a24 100%); }
  .feature--outdoor { top: 807px; }
  .feature--outdoor .copy { top: 234px; }
  .feature--outdoor .photo { background: linear-gradient(170deg, #2c3428 0%, #6f7268 40%, #9a9b96 60%, #3e5a2c 100%); }
</style>
</head>
<body>
  <svg class="backdrop" viewBox="0 0 1200 1200" aria-hidden="true">
    <path d="M0 0 C180 60 300 180 360 230 L0 230 Z" fill="#a0375a" opacity=".35"/>
    <path d="M90 0 C250 90 330 150 380 240" fill="none" stroke="#a33b5f" stroke-width="30" opacity=".3"/>
    <path d="M860 0 C980 140 1100 300 1200 360 L1200 0 Z" fill="#a0375a" opacity=".25"/>
    <path d="M760 560 C900 640 1000 740 1080 800" fill="none" stroke="#a33b5f" stroke-width="40" opacity=".25"/>
  </svg>

  <section class="rooms-intro">
    <h2>FÜR JEDEN ANSPRUCH DAS RICHTIGE ZIMMER</h2>
    <p>Alle unsere Zimmer haben einen Fernseher, freies W-Lan,<br>Handtücher liegen bereit und im Badezimmer gibt es<br>selbstverständlich Shampoo und einen Fön! Und alle<br>Sonderwünsche werden bestmöglich erfüllt!<br>Check-in Zeit ist von 17.00 - 19.00 Uhr oder nach Absprache.<br>Check-out wird in der Zeit von 08.00 - 11.00 Uhr<br>erbeten. Die Zahlung erfolgt in bar oder per EC-Karte.</p>
  </section>

  <div class="room room--blue">
    <div class="photo" role="img" aria-label="Foto Zimmer mit blauer Wand, Lederbank und Fahrradrad-Dekoration"></div>
    <div class="label">BLUE river</div>
    <div class="underline"></div>
  </div>
  <div class="room room--gold">
    <div class="photo" role="img" aria-label="Foto Zimmer mit Metallbett und gelber Decke"></div>
    <div class="label">OldGOLDmeadow</div>
    <div class="underline"></div>
  </div>
  <div class="room room--silver">
    <div class="photo" role="img" aria-label="Foto helles Zimmer mit Hängesessel, Sofa und Fensterbank"></div>
    <div class="label">SILVER Feather</div>
  </div>

  <p class="rooms-more">Weitere Informationen zu unseren Zimmern finden<br>sie auf unserer Website www.seeinn-sorpe.de!</p>

  <section class="feature feature--breakfast">
    <div class="photo" role="img" aria-label="Foto Frühstückstisch mit Omelett, Obstschale, Orangensaft und Speck"></div>
    <h3>LECKERES FRÜHSTÜCK</h3>
    <p class="copy">
      <span class="line">Das Frühstück findet im Esszimmer mit schönem Blick auf die</span>
      <span class="line">nahen Berge oder den Sorpesee statt. Bei gutem Wetter kann</span>
      <span class="line">man sogar auf dem Balkon frühstücken. Ob Rührei mit Toast,</span>
      <span class="line">Pancakes mit Ahornsirup und wahlweise Speck, Brötchen und</span>
      <span class="line">gemischte Aufschnitt- und Käseplatten.... Und natürlich frisches</span>
      <span class="line">Obst und Cerealien! In der Zeit von 08.00 – 10.30 Uhr ist hier alles</span>
      <span class="line line--last">möglich!</span>
    </p>
  </section>

  <section class="feature feature--leisure">
    <div class="photo" role="img" aria-label="Foto Wintergarten mit Kamin, rotem Sofa und Esstisch"></div>
    <h3>FREIZEIT</h3>
    <p class="copy">
      <span class="line">Wenn das Wetter einmal nicht so mitspielt, steht für die</span>
      <span class="line">Abendstunden, das Tagesabschlussgetränk oder auch einfach für</span>
      <span class="line">ein gemütliches Beisammensein ein Wintergarten zur</span>
      <span class="line">Verfügung, der sowohl über einen Kamin, als auch einen indoor-</span>
      <span class="line">Grill verfügt. In der Garage können Räder und Motorräder</span>
      <span class="line">regensicher untergestellt werden Ausflugstipps jeglicher Art</span>
      <span class="line line--last">geben wir euch gerne! Und alles ist selbstverständlich geprüft!</span>
    </p>
  </section>

  <section class="feature feature--outdoor">
    <div class="photo" role="img" aria-label="Foto Gartenlounge aus Rattan auf dem Rasen"></div>
    <h3>AUßENFLÄCHEN</h3>
    <p class="copy">
      <span class="line">Zum Wohlfühlen bieten sich bei uns viele Möglichkeiten. Da wäre</span>
      <span class="line">zunächst der riesige Garten mit 5000 qm, in dem es sowohl</span>
      <span class="line">diverse Rückzugsmöglich-keiten mit Liegen oder Gartenstühlen</span>
      <span class="line">als auch eine komplett eingezäunte Auslauffläche für die</span>
      <span class="line">vierbeinigen Gäste gibt. Eine Stelle für ein Lagerfeuer, was wir auf</span>
      <span class="line line--last">Nachfrage gern entzünden, ist selbstverständlich auch gegeben.</span>
    </p>
  </section>
</body>
</html>
```